Hartwell Estates Business Cards

I would like a business card that includes myself and my partner.
Includes: Logo, office #, email, website, our names, our numbers and possibly the address. I would also like the logo to be embossed and the card to be horizontal.
There is a photo of our yard signs to give you an idea of the colors of our business.

Target Market(s)

Everyone in real estate market.
We are in a rural area. Our clientele are from all socioeconomic backgrounds.

Industry/Entity Type

Real Estate Agent

Contact Information for Business Card

Company Name: Hartwell Estates
Our Names, Titles & Cell #'s : Dana Pembrook-Broker (555).317.6624, Marla Pembrook-Realtor (555).609.1385
Office #: (555).240.3918
Website: hartwellestates-demo.com
Joint Email: pembrook@hartwellestates-demo.com
Office Address: 418B W. Calloway Ave.
Alder Springs, ST. 70913

Font styles to use
Serif

Requirements
Must have
• HORIZONTAL, Logo, Myself and my partners names, Our cell #'s, our office #, our website, our email address
Nice to have
• Embossed logo, office address, our titles.

```html
<!DOCTYPE html>
<html lang="en">
<head>
<meta charset="utf-8">
<title>Hartwell Estates Business Cards</title>
<link rel="stylesheet" href="https://fonts.googleapis.com/css2?family=Libre+Baskerville:wght@400;700&display=swap">
<style>
  :root {
    --purple: #4b2466;
    --ink-grey: #5a5a5a;
    --card: #ffffff;
    --backdrop: #e8e6e4;
  }
  * { box-sizing: border-box; margin: 0; padding: 0; }
  html, body { width: 1200px; height: 1189px; overflow: hidden; }
  body {
    background: var(--backdrop);
    font-family: "Libre Baskerville", "Times New Roman", serif;
    position: relative;
  }
  .card {
    position: absolute;
    left: 160px;
    width: 880px;
    height: 503px;
    background: var(--card);
    overflow: hidden;
    box-shadow: 0 6px 18px rgba(0,0,0,0.12);
  }
  .card--front { top: 55px; }
  .card--back { top: 630px; }

  .brand-disc {
    position: absolute;
    left: -70px;
    top: 60px;
    width: 380px;
    height: 380px;
    border-radius: 50%;
    background: var(--purple);
  }

  .wordmark {
    position: absolute;
    right: 70px;
    top: 175px;
    text-align: right;
    color: var(--purple);
  }
  .wordmark__row { display: flex; align-items: center; justify-content: flex-end; gap: 16px; }
  .wordmark__dot { width: 30px; height: 30px; border-radius: 50%; background: var(--purple); }
  .wordmark__name {
    font-weight: 700;
    font-size: 44px;
    letter-spacing: 1px;
    border-bottom: 1.5px solid var(--purple);
    padding-bottom: 4px;
  }
  .wordmark__sub { font-weight: 700; font-size: 28px; margin-top: 6px; }
  .wordmark__url { font-size: 19px; margin-top: 14px; }

  .contact {
    position: absolute;
    left: 400px;
    top: 48px;
    width: 440px;
    color: var(--ink-grey);
    font-size: 17px;
    line-height: 1.3;
  }
  .contact__rule { border-top: 3px dotted var(--purple); margin: 14px 0; }
  .person { margin-bottom: 16px; }
  .person__name { color: var(--purple); font-weight: 700; font-size: 26px; line-height: 1.15; }
  .person__title { font-size: 17px; }
  .label { color: var(--purple); font-weight: 700; }
  .contact__office { font-size: 17px; white-space: nowrap; }
</style>
</head>
<body>
  <section class="card card--front" aria-label="Business card front">
    <div class="brand-disc"></div>
    <div class="wordmark">
      <div class="wordmark__row">
        <span class="wordmark__dot"></span>
        <span class="wordmark__name">HARTWELL</span>
      </div>
      <div class="wordmark__sub">Estates</div>
      <div class="wordmark__url">hartwellestates-demo.com</div>
    </div>
  </section>

  <section class="card card--back" aria-label="Business card back">
    <div class="brand-disc"></div>
    <div class="contact">
      <div class="contact__rule"></div>
      <p class="contact__address">418B W. Calloway Ave.<br>Alder Springs, ST. 70913</p>
      <div class="contact__rule"></div>
      <div class="person">
        <p class="person__name">Dana Pembrook</p>
        <p class="person__title">Broker</p>
        <p><span class="label">M:</span> (555).317.6624</p>
      </div>
      <div class="person">
        <p class="person__name">Marla Pembrook</p>
        <p class="person__title">Realtor</p>
        <p><span class="label">M:</span> (555).609.1385</p>
      </div>
      <div class="contact__rule"></div>
      <p class="contact__office"><span class="label">Office:</span> (555).240.3918</p>
      <p class="contact__office"><span class="label">Email:</span> pembrook@hartwellestates-demo.com</p>
    </div>
  </section>
</body>
</html>
```